Building company buisness cards

We are looking for a sharp modern new look for our business cards.We are a New Zealand based company that specialises in house and land packages.We have attached a photo of the current logo and would like to see if it can be improved somehow if needed.We are open to any colours but we have chosen Black and White at this stage. Feel free to change the font and make the logo smarter looking.Play with the colours and see what looks best.We want a card that looks so good know one will want to throw it away!

Target Market(s)

Building profesonals, home buyers

Industry/Entity Type

Building

Contact Information for Business Card

Garrick Tenwood
0275390628
garrickt@hartvale.co.nz

Font styles to use
Serif
Sans Serif

Colors

Designer to choose colors to be used in the design.

Requirements
Must have
• Just the logo on one side and details on the other
• Clean simple looking card
Nice to have
• Round corners and detail like raised or spot UV
• Something that stands out
Should not have
• To title needed, Director etc

```html
<!DOCTYPE html>
<html lang="en">
<head>
<meta charset="utf-8">
<title>Hartvale business cards</title>
<link rel="stylesheet" href="https://fonts.googleapis.com/css2?family=Playfair+Display:wght@900&family=Open+Sans:wght@400;700&display=swap">
<style>
  :root {
    --page: #2a2a2c;
    --ink: #111111;
    --paper: #ffffff;
    --card-black: #0e0e0f;
    --soft-grey: #e6e6e6;
    --mid-grey: #6b6b6b;
    --light-text: #f2f2f2;
  }
  * { box-sizing: border-box; margin: 0; padding: 0; }
  html, body { width: 1200px; height: 885px; overflow: hidden; }
  body {
    background: var(--page);
    font-family: "Open Sans", Arial, sans-serif;
    position: relative;
  }
  .card {
    position: absolute;
    left: 280px;
    width: 640px;
    height: 370px;
    border-radius: 22px;
    overflow: hidden;
  }
  .card--back { top: 45px; background: var(--card-black); }
  .card--front { top: 470px; background: var(--paper); }

  .back-mark {
    position: absolute;
    top: 120px; left: 0; right: 0;
    display: flex; align-items: center; justify-content: center; gap: 14px;
    font-family: "Playfair Display", Georgia, serif;
    font-weight: 900;
    font-size: 44px;
    color: var(--light-text);
  }
  .back-mark .dot {
    width: 26px; height: 26px; border-radius: 50%;
    border: 3px solid var(--light-text);
  }
  .back-url {
    position: absolute;
    bottom: 62px; left: 0; right: 0;
    text-align: center;
    color: var(--light-text);
    font-size: 14px;
    letter-spacing: 6px;
  }

  .front-ring {
    position: absolute;
    left: 140px; top: 150px;
    width: 440px; height: 440px;
  }
  .brand {
    position: absolute;
    top: 42px; left: 150px;
    display: flex; align-items: center; gap: 14px;
    font-family: "Playfair Display", Georgia, serif;
    font-weight: 900;
    font-size: 66px;
    line-height: 1;
    color: var(--ink);
  }
  .brand .dot {
    width: 48px; height: 48px; border-radius: 50%;
    border: 4px solid var(--ink);
  }
  .contact {
    position: absolute;
    top: 160px; right: 40px;
    list-style: none;
    font-size: 15px;
    color: var(--mid-grey);
    line-height: 1.45;
  }
  .contact li { display: flex; align-items: center; gap: 7px; }
  .contact svg { width: 13px; height: 13px; fill: var(--ink); }
  .holder {
    position: absolute;
    left: 40px; top: 272px;
    font-weight: 700;
    font-size: 20px;
    color: var(--ink);
    background: linear-gradient(to bottom, transparent 0 10%, var(--soft-grey) 10% 100%);
    padding: 2px 10px 2px 4px;
  }
</style>
</head>
<body>
  <section class="card card--back">
    <div class="back-mark"><span class="dot"></span>Hartvale</div>
    <p class="back-url">www.hartvale.co.nz</p>
  </section>

  <section class="card card--front">
    <svg class="front-ring" viewBox="0 0 440 440" aria-hidden="true">
      <circle cx="220" cy="220" r="200" fill="none" stroke="var(--soft-grey)" stroke-width="18"/>
    </svg>
    <div class="brand">Hartvale<span class="dot"></span></div>
    <ul class="contact">
      <li>
        <svg viewBox="0 0 16 16" aria-hidden="true"><path d="M3 1h3l1.5 4-2 1.2a9 9 0 0 0 4.3 4.3L11 8.5l4 1.5v3a2 2 0 0 1-2 2A12 12 0 0 1 1 3a2 2 0 0 1 2-2z"/></svg>
        0275390628
      </li>
      <li>
        <svg viewBox="0 0 16 16" aria-hidden="true"><path d="M1 3h14v10H1z M1 3l7 6 7-6" fill="var(--ink)"/><path d="M1.5 3.5l6.5 5.5 6.5-5.5" fill="none" stroke="#fff" stroke-width="1.2"/></svg>
        garrickt@hartvale.co.nz
      </li>
    </ul>
    <p class="holder">Garrick Tenwood</p>
  </section>
</body>
</html>
```